Corvane Freight Company Business Card Design

We are a company that delivers natural saltwater (from the ocean) to aquarium companies, restaurants and home marine tanks. I would like a new business card to suit.

Must include Name, company name, abn, contact number and website as well as logo (see attached).

Looking for a design that stands out, has a clean but unique appearance.

Double and single sided entries welcome

Business

• Logo

```html
<!DOCTYPE html>
<html lang="en">
<head>
<meta charset="utf-8">
<title>Corvane Freight Company – Business Card</title>
<link rel="stylesheet" href="https://fonts.googleapis.com/css2?family=Open+Sans:wght@400;600;700&display=swap">
<style>
  :root {
    --backdrop: #111111;
    --card: #ffffff;
    --brand-blue: #1a8fd1;
    --name-blue: #1b6db5;
    --tab-blue: #5cc8f2;
    --text-grey: #4a4a4a;
    --rule-grey: #b8b8b8;
  }
  * { box-sizing: border-box; margin: 0; padding: 0; }
  html, body {
    width: 1200px; height: 420px; overflow: hidden;
    background: var(--backdrop);
    font-family: "Open Sans", Arial, sans-serif;
  }
  .canvas { position: relative; width: 1200px; height: 420px; }
  .card {
    position: absolute; top: 66px;
    width: 515px; height: 294px;
    background: var(--card);
  }
  .card--front { left: 69px; }
  .card--back { left: 621px; }

  .edge-tab {
    position: absolute; top: 104px; width: 8px; height: 92px;
    background: var(--tab-blue);
  }
  .edge-tab--left { left: 0; border-radius: 0 4px 4px 0; }
  .edge-tab--right { right: 0; border-radius: 4px 0 0 4px; }

  .brand-name {
    color: var(--brand-blue);
    font-weight: 600;
    line-height: 1.08;
    text-align: center;
  }
  .card--front .brand-name {
    position: absolute; left: 24px; top: 104px; width: 230px;
    font-size: 29px;
  }
  .card--back .brand-name {
    position: absolute; left: 40px; right: 40px; top: 86px;
    font-size: 52px;
  }

  .divider {
    position: absolute; left: 269px; top: 62px;
    width: 2px; height: 172px;
    background: linear-gradient(to bottom, rgba(184,184,184,0), var(--rule-grey) 20%, var(--rule-grey) 80%, rgba(184,184,184,0));
  }

  .contact {
    position: absolute; left: 287px; top: 66px;
    color: var(--text-grey); font-size: 13px; line-height: 19px;
  }
  .contact__name { color: var(--name-blue); font-size: 18px; font-weight: 700; line-height: 22px; }
  .contact__title { font-size: 14px; margin-bottom: 13px; }
  .contact__line { display: flex; align-items: center; gap: 6px; }
  .contact__line svg { width: 10px; height: 10px; flex: none; }
  .contact__address { margin-top: 18px; }
</style>
</head>
<body>
<main class="canvas">
  <section class="card card--front" aria-label="Card front">
    <span class="edge-tab edge-tab--left"></span>
    <span class="edge-tab edge-tab--right"></span>

    <p class="brand-name">Corvane Freight Company</p>

    <span class="divider"></span>

    <div class="contact">
      <p class="contact__name">Your Name</p>
      <p class="contact__title">Title</p>
      <p class="contact__line">
        <svg viewBox="0 0 10 10" aria-hidden="true"><path d="M2 0.8 L3.6 2.6 L2.7 3.8 Q3.8 6 6.2 7.3 L7.4 6.4 L9.2 8 Q8.4 9.6 6.8 9.2 Q1.6 7.4 0.8 2.4 Q0.6 1.2 2 0.8Z" fill="#4a4a4a"/></svg>
        123-456-7892
      </p>
      <p class="contact__line">
        <svg viewBox="0 0 10 10" aria-hidden="true"><g fill="none" stroke="#4a4a4a" stroke-width="1"><circle cx="5" cy="5" r="4.3"/><ellipse cx="5" cy="5" rx="1.9" ry="4.3"/><path d="M0.7 5 H9.3 M1.5 2.7 H8.5 M1.5 7.3 H8.5"/></g></svg>
        www.corvanefreight.com
      </p>
      <p class="contact__address">Street Name, City Name ,<br>State, Zip Code<br>ABN: 123456789</p>
    </div>
  </section>

  <section class="card card--back" aria-label="Card back">
    <p class="brand-name">Corvane Freight Company</p>
  </section>
</main>
</body>
</html>
```